Design a business card
Business name: Harbourline Growth Advisory
Improving Business Profitibility

- An Overview of the Business & Service:

Business Performance Consulting

- The Target Market: Small to medium-sized business

- Design Specifics:
White card, blue ink, moon eclipse

No Logo

Target Market(s)

Small to medium-sized business

Font styles to use
Sans Serif

```html
<!DOCTYPE html>
<html lang="en">
<head>
<meta charset="utf-8">
<title>Harbourline Growth Advisory – Business Card</title>
<link rel="stylesheet" href="https://fonts.googleapis.com/css2?family=Tinos&family=Questrial&display=swap">
<style>
  :root {
    --page-bg: #e6e6e8;
    --card-white: #f7f7f6;
    --ink-blue: #1f3a7a;
    --ink-dark: #1b1b1b;
    --rule-grey: #4a4a4a;
    --moon-light: #dadada;
    --moon-mid: #c2c2c2;
    --moon-dark: #a6a6a6;
  }
  * { box-sizing: border-box; margin: 0; padding: 0; }
  html, body {
    width: 1200px;
    height: 922px;
    overflow: hidden;
    background: var(--page-bg);
  }
  .card {
    position: absolute;
    left: 100px;
    top: 175px;
    width: 1000px;
    height: 572px;
    background: var(--card-white);
    overflow: hidden;
    box-shadow: 0 6px 24px rgba(0,0,0,0.18);
  }
  .moon {
    position: absolute;
    inset: 0;
    width: 1000px;
    height: 572px;
  }
  .wordmark {
    position: absolute;
    left: 62px;
    top: 222px;
    width: 400px;
    font-family: "Tinos", "Times New Roman", serif;
    font-weight: 400;
    color: var(--ink-blue);
    line-height: 1;
    white-space: nowrap;
  }
  .wordmark-main {
    display: block;
    font-size: 54px;
    letter-spacing: 0;
  }
  .wordmark-sub {
    display: block;
    font-size: 28px;
    margin-top: 4px;
    padding-left: 36px;
  }
  .divider {
    position: absolute;
    left: 492px;
    top: 118px;
    width: 2px;
    height: 172px;
    background: var(--rule-grey);
  }
  .contact {
    position: absolute;
    left: 526px;
    top: 116px;
    list-style: none;
    font-family: "Questrial", "Century Gothic", sans-serif;
    font-size: 21px;
    color: var(--ink-dark);
    line-height: 1.2;
  }
  .contact-item {
    display: flex;
    align-items: flex-start;
    gap: 16px;
    margin-bottom: 6px;
  }
  .contact-icon {
    width: 16px;
    height: 22px;
    flex: none;
    margin-top: 1px;
  }
  .person-name {
    position: absolute;
    left: 558px;
    top: 380px;
    font-family: "Tinos", "Times New Roman", serif;
    font-size: 28px;
    color: var(--ink-dark);
  }
</style>
</head>
<body>
  <main class="card">
    <svg class="moon" viewBox="0 0 1000 572" role="img" aria-label="Photograph of the cratered grey surface of the full moon rising from the bottom of the card">
      <defs>
        <radialGradient id="moonShade" cx="0.5" cy="0.45" r="0.55">
          <stop offset="0" stop-color="var(--moon-dark)"/>
          <stop offset="0.6" stop-color="var(--moon-mid)"/>
          <stop offset="1" stop-color="var(--moon-light)"/>
        </radialGradient>
      </defs>
      <circle cx="700" cy="690" r="420" fill="url(#moonShade)"/>
    </svg>

    <div class="wordmark">
      <span class="wordmark-main">HARBOURLINE</span>
      <span class="wordmark-sub">Growth Advisory</span>
    </div>

    <div class="divider"></div>

    <ul class="contact">
      <li class="contact-item">
        <svg class="contact-icon" viewBox="0 0 16 22" aria-hidden="true">
          <rect x="3" y="1" width="10" height="18" rx="2" fill="none" stroke="var(--ink-blue)" stroke-width="2"/>
          <rect x="5" y="4" width="6" height="8" fill="var(--ink-blue)"/>
        </svg>
        <span>(418) 902-3365</span>
      </li>
      <li class="contact-item">
        <svg class="contact-icon" viewBox="0 0 16 22" aria-hidden="true">
          <path d="M4 4 C2 6 2 10 5 14 C8 18 11 19 13 17 L11 14 L9 15 C7 14 6 12 6 10 L8 9 L7 5 Z" fill="var(--ink-blue)"/>
        </svg>
        <span>(418) 902-3365</span>
      </li>
      <li class="contact-item">
        <svg class="contact-icon" viewBox="0 0 16 22" aria-hidden="true">
          <path d="M8 2 C4 2 2 5 2 8 C2 12 8 19 8 19 C8 19 14 12 14 8 C14 5 12 2 8 2 Z" fill="var(--ink-blue)"/>
          <circle cx="8" cy="8" r="2.3" fill="var(--card-white)"/>
        </svg>
        <span>327-1145 Merrow Ln.<br>Eastbrook Vermont 05831</span>
      </li>
    </ul>

    <p class="person-name">Desmond R Akerly</p>
  </main>
</body>
</html>
```